Website Design for Videographer

I am looking to update my website - www.brinolvaske.com. I am a wedding videographer who specialises in natural and documentary videography.

The website will be built by my designer using the Wordpress Plinthworx framework.

Requirements;
I want the website to have a clean white look mixed in with video footage.
Needs to be classy. At the moment my website uses a lot of Gold. On the new look I DO NOT want gold.

Need a web and mobile design for the following 12 pages;

* Home page (need to have example videos and text)
* About (this is about me and my service)
* Videos (examples of my work)
* Testimonials
* Packages
* Contact
* Content (this is to show social media content that I am making in a vertical format and advertise this service).
* Blog (index page for blog)
* Blog pages (individual pages for blog content)
* Wedding Venues Index Page (https://brinolvaske.com/north-east-wedding-venues/)
* Individual venue pages (https://brinolvaske.com/north-east-wedding-venues/marlow-tendle-lodge-wedding-videos/) - Needs to show videos, photos, text as is on the current page.
* Venue Tours (https://brinolvaske.com/wedding-venue-tours/)

My current logo is attached however on the website I want to go for a black and white style for it.

Example styles I like however must not be copied.
https://joswelbrant.co.uk/about/
https://oakandripple.co.uk/ (if done in white)
https://tumblemothpictures.co.uk/

Target Market(s)

Couples getting married aged 25-35

Industry/Entity Type

Weddings

Number of Pages Required

5+ page

Font styles to use
Sans Serif

Requirements
Must have
• A classy look, black and white, use videos and photos.
Should not have
• Gold colour

```html
<!DOCTYPE html>
<html lang="en">
<head>
<meta charset="utf-8">
<title>Brin Olvaske — North East Wedding Videographer</title>
<link href="https://fonts.googleapis.com/css2?family=Plus+Jakarta+Sans:wght@400;500;600;700;800&display=swap" rel="stylesheet">
<style>
:root{
  --black:#000;
  --ink:#111114;
  --white:#fff;
  --grey:#4a4a4a;
  --muted:#8a8a8a;
  --line:#5a5a5a;
  --soft:#e9e9e9;
  --peach:#f3c9a0;
  --font:"Plus Jakarta Sans", Arial, sans-serif;
}
*{box-sizing:border-box;margin:0;padding:0}
html,body{width:1200px;height:4743px;overflow:hidden}
body{position:relative;font-family:var(--font);color:var(--ink);background:var(--white)}
.abs{position:absolute}
.band{position:absolute;left:0;width:1200px}
.dark{background:var(--black);color:var(--white)}

/* nav */
.nav{top:0;height:83px}
.brand{left:53px;top:30px;font-size:13px;font-weight:700;letter-spacing:2px;text-transform:uppercase;color:var(--white)}
.brand-mark{display:inline-block;width:10px;height:10px;border:1.5px solid var(--white);margin-right:8px;vertical-align:middle}
.nav-links{top:33px;left:508px;display:flex;font-size:13px;color:var(--white)}
.nav-links span{position:absolute;white-space:nowrap}

/* hero */
.hero-eyebrow{left:53px;top:211px;font-size:11px}
.hero-title{left:53px;top:258px;font-size:40px;line-height:47px;font-weight:800;letter-spacing:-.5px;text-transform:uppercase}
.hero-text{left:53px;top:360px;width:370px;font-size:13px;line-height:21px}
.btn-dark{background:var(--ink);color:var(--white);font-size:12px;font-weight:600;display:flex;align-items:center;justify-content:center;border-radius:3px}
.hero-cta{left:53px;top:482px;width:125px;height:34px}
.hero-photo{left:592px;top:147px;width:608px;height:567px;border-radius:44px 0 0 0;background:linear-gradient(135deg,#c9bda9 0%,#efe9df 40%,#d9cbb4 65%,#8e7a5e 100%)}
.booking{left:53px;top:644px;width:1055px;height:109px;background:var(--black);border-radius:6px;color:var(--white)}
.field{position:absolute;top:36px}
.field b{display:block;font-size:12px;font-weight:600}
.field small{font-size:9px;color:#cfcfcf}
.field svg{margin-left:14px;vertical-align:middle}
.booking-btn{position:absolute;left:898px;top:36px;width:117px;height:34px;background:var(--white);color:var(--ink);font-size:12px;font-weight:600;border-radius:3px;display:flex;align-items:center;justify-content:center}

/* awards */
.h2{position:absolute;left:0;width:1200px;text-align:center;font-size:40px;font-weight:500;letter-spacing:-.8px}
.sub{position:absolute;text-align:center;font-size:14px;line-height:22px}
.award-icon{position:absolute;top:1010px;width:88px;height:88px;border-radius:18px;background:var(--black);display:flex;align-items:center;justify-content:center}
.award-title{position:absolute;top:1128px;width:300px;text-align:center;font-size:19px;font-weight:500}
.award-text{position:absolute;top:1163px;width:230px;text-align:center;font-size:11px;line-height:21px;color:var(--grey)}

/* films */
.tabs{left:61px;top:1585px;width:1093px}
.tab{position:absolute;top:0;font-size:17px;width:546px;text-align:center}
.tab.off{color:var(--muted)}
.tab-rule{position:absolute;top:47px;height:2px}
.film{position:absolute;top:1674px;width:252px;height:322px;border-radius:3px}
.film .heart{position:absolute;right:14px;top:18px}
.film .play{position:absolute;left:106px;top:140px;width:40px;height:40px;border-radius:50%;background:var(--black);display:flex;align-items:center;justify-content:center}
.film .play.on{background:var(--peach)}
.film .play-btn{position:absolute;right:18px;bottom:20px;width:92px;height:30px;background:var(--white);color:var(--ink);font-size:12px;font-weight:500;border-radius:2px;display:flex;align-items:center;justify-content:center}
.approach{left:70px;top:2082px;width:1062px;text-align:center;font-size:15.5px;line-height:25px;color:var(--white)}
.btn-light{left:535px;top:2401px;width:129px;height:37px;background:var(--white);color:var(--ink);font-size:12px;font-weight:500;border-radius:3px;display:flex;align-items:center;justify-content:center}

/* north east */
.ne-photo{left:83px;top:2723px;width:471px;height:440px;background:linear-gradient(160deg,#7c8a6a 0%,#b7a994 40%,#e9e6df 62%,#6f6558 100%)}
.ne-text{left:611px;top:2727px;width:526px;font-size:15px;line-height:25px;color:var(--ink)}

/* gallery */
.gallery-img{position:absolute;top:3305px;width:534px;height:298px;border-radius:3px}

/* reviews */
.rev-kicker{left:0;width:1200px;top:3772px;text-align:center;font-size:28px;font-weight:600}
.rev-title{left:0;width:1200px;top:3814px;text-align:center;font-size:28px;font-weight:700}
.review{position:absolute;top:3965px;width:334px;height:190px;background:var(--black);color:var(--white);border-radius:6px;padding:26px 26px}
.avatar{position:absolute;left:34px;top:24px;width:32px;height:32px;border-radius:50%;background:linear-gradient(135deg,#d8c3b0,#6c5a4d)}
.rev-name{position:absolute;left:84px;top:24px;font-size:13px;font-weight:600}
.rev-place{position:absolute;left:90px;top:44px;font-size:10px;color:#cfcfcf}
.rev-body{position:absolute;left:26px;top:84px;width:290px;font-size:11.5px;line-height:25px}
.dots{left:59px;top:4225px;display:flex;gap:7px;align-items:center}
.dots i{display:block;width:10px;height:10px;border-radius:50%;background:#d6d6dc}
.dots i.on{width:36px;border-radius:6px;background:#1d1d2b}

/* footer */
.footer{top:4339px;height:404px}
.foot-brand{left:78px;top:4478px;font-size:16px;font-weight:600;letter-spacing:3px;color:var(--white);text-transform:uppercase}
.socials{left:89px;top:4526px;display:flex;gap:19px}
.socials i{display:block;width:26px;height:26px;border-radius:50%;background:var(--white)}
.foot-col{position:absolute;color:var(--white);font-size:13px;line-height:31px}
.foot-col h4{font-size:16px;font-weight:500;line-height:24px;margin-bottom:4px}
.foot-col p{font-size:12.5px}
.foot-base{top:4675px;font-size:12px;color:var(--white)}
</style>
</head>
<body>

<!-- Navigation -->
<header class="band dark nav">
  <div class="abs brand"><span class="brand-mark"></span>Brin Olvaske</div>
  <nav class="abs nav-links" style="left:0;width:1200px">
    <span style="left:508px">Home</span>
    <span style="left:587px">About</span>
    <span style="left:676px">Portfolio</span>
    <span style="left:774px">Testimonials</span>
    <span style="left:917px">Insight</span>
    <span style="left:1018px">Contact</span>
  </nav>
</header>

<!-- Hero -->
<section>
  <p class="abs hero-eyebrow">Brin Olvaske</p>
  <h1 class="abs hero-title">North East Wedding<br>Videographer</h1>
  <p class="abs hero-text">A trusted and acclaimed North East wedding videographer who has more than 25 years of videography experience.</p>
  <div class="abs btn-dark hero-cta">Booking Now</div>
  <div class="abs hero-photo" role="img" aria-label="Close-up of wedding rings resting on white roses with baby's breath"></div>
  <div class="abs booking">
    <div class="field" style="left:72px"><b>Locations</b><small>Select your city</small><svg width="10" height="6" viewBox="0 0 10 6"><path d="M1 1l4 4 4-4" fill="none" stroke="#fff" stroke-width="1.4"/></svg></div>
    <div class="field" style="left:378px"><b>Date</b><small>Select your date</small><svg width="10" height="6" viewBox="0 0 10 6"><path d="M1 1l4 4 4-4" fill="none" stroke="#fff" stroke-width="1.4"/></svg></div>
    <div class="field" style="left:690px"><b>Time</b><small>Select your time</small><svg width="10" height="6" viewBox="0 0 10 6"><path d="M1 1l4 4 4-4" fill="none" stroke="#fff" stroke-width="1.4"/></svg></div>
    <div class="booking-btn">Booking Now</div>
  </div>
</section>

<!-- Awards -->
<section>
  <h2 class="h2" style="top:840px">Vowline Wedding Awards 2024 Winner</h2>
  <p class="sub" style="left:370px;width:460px;top:921px">Award-Winning Videographer from North East, Customer Satisfaction and Votes as Key to Success</p>

  <div class="award-icon" style="left:135px">
    <svg width="44" height="44" viewBox="0 0 44 44" fill="#fff"><path d="M12 6h20v10a10 10 0 0 1-20 0z"/><path d="M12 9H6v4a7 7 0 0 0 7 7M32 9h6v4a7 7 0 0 1-7 7" fill="none" stroke="#fff" stroke-width="2.5"/><rect x="19" y="25" width="6" height="7"/><rect x="13" y="32" width="18" height="5" rx="1"/></svg>
  </div>
  <div class="award-icon" style="left:556px">
    <svg width="44" height="40" viewBox="0 0 44 40"><path d="M22 38S3 26 3 13A10 10 0 0 1 22 8a10 10 0 0 1 19 5c0 13-19 25-19 25z" fill="#fff"/></svg>
  </div>
  <div class="award-icon" style="left:973px">
    <svg width="44" height="44" viewBox="0 0 44 44"><circle cx="22" cy="22" r="18" fill="#fff"/><circle cx="22" cy="22" r="5" fill="#000"/><path d="M22 9a13 13 0 0 0-13 13" fill="none" stroke="#000" stroke-width="3"/><path d="M35 22a13 13 0 0 1-13 13" fill="none" stroke="#000" stroke-width="3"/></svg>
  </div>
  <svg class="abs" style="left:240px;top:1010px" width="720" height="80" viewBox="0 0 720 80" fill="none" stroke="#333" stroke-width="1.2">
    <path d="M4 74c60 2 90-6 130-40s80-14 66-30"/>
    <path d="M420 74c60 2 90-6 130-40s80-14 66-30"/>
  </svg>

  <h3 class="award-title" style="left:29px">Regional Recognition</h3>
  <h3 class="award-title" style="left:450px;top:1125px">Customer Endorsement</h3>
  <h3 class="award-title" style="left:870px">Memorable Moments</h3>
  <p class="award-text" style="left:64px">Being the only wedding videographer from the North East to win the Vowline Wedding Awards 2024 is a huge honor.</p>
  <p class="award-text" style="left:485px;top:1158px">What makes this award even more special is that it's not just based on industry standards but on the votes and testimonials from the couples I've worked with</p>
  <p class="award-text" style="left:903px;top:1160px">The award stands as a testament to the beautiful memories I've been able to capture on film. Each wedding has been a unique story</p>
</section>

<!-- Films -->
<section class="band dark" style="top:1321px;height:1191px"></section>
<section style="color:var(--white)">
  <h2 class="h2" style="top:1412px;color:var(--white)">Wedding Videography For Natural Moments</h2>
  <p class="sub" style="left:370px;width:460px;top:1475px;color:var(--white)">Here are a selection of video, audio and written messages from couples.</p>
  <div class="abs tabs">
    <span class="tab" style="left:0">Video</span>
    <span class="tab off" style="left:547px">Photos</span>
    <span class="tab-rule" style="left:0;width:1093px;background:var(--line);height:1px;top:48px"></span>
    <span class="tab-rule" style="left:0;width:546px;background:var(--white);top:46px;height:3px"></span>
  </div>

  <article class="film" style="left:61px;background:linear-gradient(160deg,#a6927a,#d9cdbd 55%,#8d9aa8)" role="img" aria-label="Couple embracing beneath a floral wedding arch">
    <svg class="heart" width="20" height="18" viewBox="0 0 20 18"><path d="M10 16.5S1.5 11 1.5 5.5A4.2 4.2 0 0 1 10 3.8a4.2 4.2 0 0 1 8.5 1.7C18.5 11 10 16.5 10 16.5z" fill="none" stroke="#fff" stroke-width="1.3"/></svg>
    <span class="play on"><svg width="12" height="14" viewBox="0 0 12 14"><path d="M1 1l10 6-10 6z" fill="#fff"/></svg></span>
    <span class="play-btn">Play Now</span>
  </article>
  <article class="film" style="left:341px;background:linear-gradient(160deg,#4a3a30,#8c7a68 50%,#e2ddd4)" role="img" aria-label="Bride holding a bouquet beside a rustic doorway">
    <svg class="heart" width="20" height="18" viewBox="0 0 20 18"><path d="M10 16.5S1.5 11 1.5 5.5A4.2 4.2 0 0 1 10 3.8a4.2 4.2 0 0 1 8.5 1.7C18.5 11 10 16.5 10 16.5z" fill="none" stroke="#fff" stroke-width="1.3"/></svg>
    <span class="play"><svg width="12" height="14" viewBox="0 0 12 14"><path d="M1 1l10 6-10 6z" fill="#fff"/></svg></span>
    <span class="play-btn">Play Now</span>
  </article>
  <article class="film" style="left:620px;background:linear-gradient(180deg,#d8dcdd,#ecebe6 55%,#9a9c98)" role="img" aria-label="Couple kissing on a pale coastal backdrop">
    <svg class="heart" width="20" height="18" viewBox="0 0 20 18"><path d="M10 16.5S1.5 11 1.5 5.5A4.2 4.2 0 0 1 10 3.8a4.2 4.2 0 0 1 8.5 1.7C18.5 11 10 16.5 10 16.5z" fill="none" stroke="#555" stroke-width="1.3"/></svg>
    <span class="play"><svg width="12" height="14" viewBox="0 0 12 14"><path d="M1 1l10 6-10 6z" fill="#fff"/></svg></span>
    <span class="play-btn">Play Now</span>
  </article>
  <article class="film" style="left:900px;background:linear-gradient(160deg,#3f4a2e,#c3a57a 45%,#5a3a32 80%,#b9a9a0)" role="img" aria-label="Couple embracing among autumn trees at sunset">
    <svg class="heart" width="20" height="18" viewBox="0 0 20 18"><path d="M10 16.5S1.5 11 1.5 5.5A4.2 4.2 0 0 1 10 3.8a4.2 4.2 0 0 1 8.5 1.7C18.5 11 10 16.5 10 16.5z" fill="none" stroke="#fff" stroke-width="1.3"/></svg>
    <span class="play"><svg width="12" height="14" viewBox="0 0 12 14"><path d="M1 1l10 6-10 6z" fill="#fff"/></svg></span>
    <span class="play-btn">Play Now</span>
  </article>

  <p class="abs approach">My approach to wedding videography is straightforward: I let you and your guests enjoy the pleasure, love, and festivities of the day. The focus will be on capturing the spontaneous, real interactions that make your wedding so unique. When you look back on your wedding day, I want you to remember the genuine smiles, genuine laughing, and spontaneous moments of emotion that you might have missed in the flurry of events. The celebration of your love story… and you'll want to remember it for the rest of your lives.<br>Your wedding film is the best way to keep this day alive forever … a newlywed's gift that keeps giving … an infinite reminder of those special moments and memories.<br>Everything about your wedding day belongs to you, the couple. Your story. Your vibe. Your friends and family. Your pre-wedding jitters. Your tears. Your laughter. Your vows. Your excitement. Your first dance. Everything. And I'm passionate about creating a wedding film that captures the very essence of your day and turning it into a family heirloom you'll treasure forever.</p>
  <div class="abs btn-light">Show more</div>
</section>

<!-- North East -->
<section>
  <h2 class="h2" style="top:2582px;font-size:40px">I LOVE THE NORTH EAST</h2>
  <p class="sub" style="left:360px;width:480px;top:2640px;color:var(--grey)">It's an honour to work as a wedding videographer in the North East of England. It's truly like living the dream. Imagine,</p>
  <div class="abs ne-photo" role="img" aria-label="Bride and groom walking hand in hand past a stone house"></div>
  <p class="abs ne-text">The North East isn't just a place on the map for me; it's a canvas where love stories come to life. And that's where my videography skills come into play. Think about it, we've got everything from historic Durham Cathedral to the iconic Tyne Bridge as backdrops. Plus, there's something magical about North East weddings, whether it's a rustic affair in a barn or an elegant ceremony in a county house.<br>Of course, the real magic happens when I get to combine my love for the North East with my passion for filming weddings. The rich history of Durham, the vibrant culture of Newcastle, and the stunning beaches of Northumberland add layers to each wedding video I produce. It's like making a mini-movie where every scene is filled with genuine emotion and the setting is as iconic as it gets.<br>So, yeah, being a North East wedding videographer is more than a job for me; it's a way of life. I wouldn't trade it for anything else. Because, at the end of the day, I'm doing what I love in a place that I love, while helping people relive the most incredible day of their lives. Does it get any better than that? I don't think so.</p>
</section>

<!-- Gallery -->
<section class="band dark" style="top:3224px;height:460px">
  <div class="gallery-img" style="left:50px;top:81px;background:linear-gradient(150deg,#c7bba9,#e8e2d6 45%,#3a3a3a 70%,#d9d4cc)" role="img" aria-label="Groom in a tuxedo and bride walking outside a stately stone house"></div>
  <div class="gallery-img" style="left:609px;top:81px;background:linear-gradient(100deg,#9aa3a6,#d2b7a0 45%,#8aa59a 65%,#c9a86a)" role="img" aria-label="Couple resting foreheads together in a golden field"></div>
</section>

<!-- Reviews -->
<section>
  <h2 class="abs rev-kicker">wedding reviews</h2>
  <h2 class="abs rev-title">Reviews From Real Couples</h2>
  <p class="sub" style="left:230px;width:740px;top:3858px;color:var(--grey)">have been invited to some amazing weddings all over the North East, UK and Europe. My main aim is to ensure that couples enjoy their day and that they take in the moments so they remember them.</p>

  <article class="review" style="left:57px">
    <span class="avatar" role="img" aria-label="Portrait of the couple"></span>
    <span class="rev-name">Harriet and Owen</span>
    <span class="rev-place">Fernbrook Hall, Northumberland</span>
    <p class="rev-body">We've just sat and watched the highlight film in our honeymoon suite. It was lush to be able to relive the day. It was absolutely brilliant and thank you for the fast turnaround.</p>
  </article>
  <article class="review" style="left:432px">
    <span class="avatar" role="img" aria-label="Portrait of the couple"></span>
    <span class="rev-name">Lena and Marcus</span>
    <span class="rev-place">Alder Falls, Lake District</span>
    <p class="rev-body">Just want to say a massive thank you for being our videographer. The films are absolutely amazing and we will treasure them forever.</p>
  </article>
  <article class="review" style="left:808px">
    <span class="avatar" role="img" aria-label="Portrait of the reviewer"></span>
    <span class="rev-name">Tomek Rudzik</span>
    <span class="rev-place">Warsaw, Poland</span>
    <p class="rev-body">"Wow... I am very happy to use this VPN, it turned out to be more than my expectations and so far there have been no problems. Quillnet always the best".</p>
  </article>

  <div class="abs dots"><i class="on"></i><i></i><i></i><i></i></div>
  <svg class="abs" style="left:907px;top:4222px" width="22" height="16" viewBox="0 0 22 16"><path d="M21 8H2M8 1L1 8l7 7" fill="none" stroke="#111" stroke-width="1.8"/></svg>
  <svg class="abs" style="left:974px;top:4222px" width="22" height="16" viewBox="0 0 22 16"><path d="M1 8h19M14 1l7 7-7 7" fill="none" stroke="#111" stroke-width="1.8"/></svg>
</section>

<!-- Footer -->
<footer class="band dark footer"></footer>
<div class="abs foot-brand">Brin Olvaske</div>
<div class="abs socials"><i></i><i></i><i></i></div>
<div class="foot-col" style="left:418px;top:4420px">
  <h4>Contact</h4>
  <p>07700 900 418</p>
  <p>films@brinolvaske.com</p>
</div>
<div class="foot-col" style="left:624px;top:4410px">
  <h4>Links</h4>
  <p>FAQ's</p>
  <p>Commercial Videography</p>
  <p>Free Speeches Guide</p>
  <p>Blog</p>
  <p>Los Island Wedding</p>
  <p>Lake Distric Wedding Videos</p>
</div>
<div class="foot-col" style="left:892px;top:4420px">
  <p>North Easth Wedding Venues</p>
  <p>Newcastle Wedding Videographer</p>
  <p>Northumberland Wedding Videos</p>
  <p>North Yorkshire Weddings</p>
  <p>Wedding Venue Tours</p>
  <p>Durham Wedding Videographer</p>
</div>
<p class="abs foot-base" style="left:78px">©2024 Brin Olvaske. All rights reserved</p>
<p class="abs foot-base" style="left:645px">Privacy &amp; Policy</p>
<p class="abs foot-base" style="left:1036px">Terms &amp; Condition</p>

</body>
</html>
```